Marwick Family Chiropractic Stationary

The letterhead and business card must have our logo.
We would like to see the logo used in different ways ( It can be expanded upon in the stationary.)
Please use the the same or similar colors.
Must be eye catching and memorable.
Must be easy to read

Reason: The doctor has been too busy to make any final decisions. He would like to give himself a little more time.

Target Market(s)

Chiropractic Healthcare

Industry/Entity Type

Business

Requirements
Must have
• Dr. Leonard Marwick D.C.
Chiropractor

860-555-0183

417 Birchfield Road, Suite 2
Brenton Falls, ME 04091

drmarwick@marwickspine.example
www.marwickspine.example
www.facebook.com/MarwickFamilySpine
Should not have
• should not be difficult to read

```html
<!DOCTYPE html>
<html lang="en">
<head>
<meta charset="utf-8">
<title>Marwick Family Chiropractic – Business Card Set</title>
<link rel="stylesheet" href="https://fonts.googleapis.com/css2?family=Montserrat:wght@600;700&family=PT+Sans:ital,wght@0,400;0,700;1,700&display=swap">
<style>
  :root {
    --stage: #efeae4;
    --label: #2a2520;
    --card-white: #ffffff;
    --card-brown: #231b14;
    --card-black: #070707;
    --brand-green: #2a9a48;
    --leaf-green: #9ccc5a;
    --bark: #2b2118;
    --bark-light: #9a8f85;
    --ink: #3a3a3a;
    --ink-strong: #2b2b2b;
    --rule: #c8c8c8;
    --light-text: #f4f4f4;
  }
  * { margin: 0; padding: 0; box-sizing: border-box; }
  html, body { width: 1200px; height: 788px; overflow: hidden; }
  body {
    position: relative;
    background: var(--stage);
    font-family: "PT Sans", Arial, sans-serif;
  }
  .view-label {
    position: absolute;
    width: 525px;
    text-align: center;
    font-size: 21px;
    color: var(--label);
  }
  .card {
    position: absolute;
    width: 525px;
    height: 300px;
    border-radius: 20px;
    overflow: hidden;
    box-shadow: 0 6px 14px rgba(0,0,0,.22);
  }
  .card--white { background: var(--card-white); }
  .card--brown { background: var(--card-brown); }
  .card--black { background: var(--card-black); }

  .mark-dot { position: absolute; border-radius: 50%; }
  .wordmark {
    position: absolute;
    width: 260px;
    text-align: center;
    font-family: "Montserrat", Arial, sans-serif;
    font-weight: 700;
    line-height: 1;
    white-space: nowrap;
  }
  .wordmark .name { display: block; }
  .wordmark .tagline { display: block; }

  .site-url {
    position: absolute;
    left: 0; width: 100%;
    text-align: center;
    font-size: 16px;
  }

  /* front */
  .front-divider {
    position: absolute;
    left: 260px; top: 56px;
    width: 2px; height: 146px;
    background: linear-gradient(to bottom, transparent, var(--rule) 30%, var(--rule) 70%, transparent);
  }
  .contact-list {
    position: absolute;
    left: 300px; top: 82px;
    list-style: none;
    font-size: 12px;
    letter-spacing: -0.1px;
    color: var(--ink);
    line-height: 22.5px;
    white-space: nowrap;
  }
  .contact-list b { font-style: italic; font-weight: 700; color: var(--ink-strong); }
  .contact-list .address { line-height: 16px; padding-top: 3px; }
  .name-band {
    position: absolute;
    left: 0; bottom: 0;
    width: 100%; height: 38px;
    background: var(--brand-green);
    color: #fff;
    text-align: center;
    line-height: 38px;
    font-family: "Montserrat", Arial, sans-serif;
    font-weight: 600;
    font-size: 13.5px;
  }
  .name-band small { font-size: 11.5px; }
</style>
</head>
<body>

  <!-- Front -->
  <div class="view-label" style="left:60px; top:33px;">Front</div>
  <section class="card card--white" style="left:60px; top:78px;">
    <span class="mark-dot" style="left:80px; top:44px; width:100px; height:100px; background:var(--brand-green);"></span>
    <div class="wordmark" style="left:0; top:182px; color:var(--brand-green);">
      <span class="name" style="font-size:32px;">MARWICK</span>
      <span class="tagline" style="font-size:12.5px; margin-top:5px; color:var(--bark);">FAMILY CHIROPRACTIC</span>
    </div>
    <div class="front-divider"></div>
    <ul class="contact-list">
      <li><b>phone :</b> 860-555-0183</li>
      <li><b>email :</b> drmarwick@marwickspine.example</li>
      <li><b>web :</b> www.marwickspine.example</li>
      <li><b>facebook :</b> MarwickFamilySpine</li>
      <li class="address"><b>add :</b> 417 Birchfield Road<br>Suite 2, Brenton Falls, ME 04091</li>
    </ul>
    <div class="name-band">Dr. Leonard Marwick D.C., <small>Chiropractor</small></div>
  </section>

  <!-- Back 1 -->
  <div class="view-label" style="left:622px; top:33px;">Back - 1</div>
  <section class="card card--white" style="left:622px; top:74px;">
    <span class="mark-dot" style="left:213px; top:32px; width:100px; height:100px; background:var(--brand-green);"></span>
    <div class="wordmark" style="left:132px; top:168px; color:var(--brand-green);">
      <span class="name" style="font-size:32px;">MARWICK</span>
      <span class="tagline" style="font-size:12.5px; margin-top:5px; color:var(--bark);">FAMILY CHIROPRACTIC</span>
    </div>
    <div class="site-url" style="top:259px; color:var(--ink);">www.marwickspine.example</div>
  </section>

  <!-- Back 2 -->
  <div class="view-label" style="left:54px; top:404px;">Back - 2</div>
  <section class="card card--brown" style="left:54px; top:445px;">
    <span class="mark-dot" style="left:157px; top:40px; width:210px; height:210px; background:rgba(255,255,255,.05);"></span>
    <div class="wordmark" style="left:12px; width:500px; top:96px; color:var(--brand-green);">
      <span class="name" style="font-size:58px;">MARWICK</span>
      <span class="tagline" style="font-size:25px; margin-top:12px; color:var(--light-text);">FAMILY CHIROPRACTIC</span>
    </div>
    <div class="site-url" style="top:260px; color:var(--light-text);">www.marwickspine.example</div>
  </section>

  <!-- Back 3 -->
  <div class="view-label" style="left:622px; top:404px;">Back - 3</div>
  <section class="card card--black" style="left:622px; top:445px;">
    <span class="mark-dot" style="left:213px; top:34px; width:100px; height:100px; background:var(--leaf-green);"></span>
    <div class="wordmark" style="left:132px; top:172px; color:var(--leaf-green);">
      <span class="name" style="font-size:32px;">MARWICK</span>
      <span class="tagline" style="font-size:12.5px; margin-top:5px; color:var(--bark-light);">FAMILY CHIROPRACTIC</span>
    </div>
    <div class="site-url" style="top:260px; color:var(--light-text);">www.marwickspine.example</div>
  </section>

</body>
</html>
```